Accounting firm needing business card / letterhead designed
Marcus L. Trenholm, CPA
marcus@veltrowledger.com
www.veltrowledger.com
842 E Alder Ave Corwin Falls, MN 43827
419-562-0974

```html
<!DOCTYPE html>
<html lang="en">
<head>
<meta charset="utf-8">
<title>Veltrow Ledger – Business Card</title>
<link rel="stylesheet" href="https://fonts.googleapis.com/css2?family=Roboto:wght@400;700&family=Roboto+Condensed:wght@700&display=swap">
<style>
  :root {
    --navy: #241f5c;
    --green: #80bd3a;
    --paper: #f7f7f6;
    --ink: #3d3d45;
    --backdrop: #e4e4e4;
    --white: #ffffff;
  }
  * { margin: 0; padding: 0; box-sizing: border-box; }
  html, body { width: 1200px; height: 960px; overflow: hidden; }
  body {
    background: var(--backdrop);
    font-family: "Roboto", Arial, sans-serif;
    position: relative;
  }
  .card {
    position: absolute;
    width: 600px;
    height: 343px;
    box-shadow: 0 2px 6px rgba(0,0,0,0.25);
    overflow: hidden;
  }
  .card--front { left: 314px; top: 113px; background: var(--paper); }
  .card--back  { left: 311px; top: 472px; background: var(--navy); }

  .wordmark {
    position: absolute;
    left: 0; right: 0;
    display: flex;
    justify-content: center;
    align-items: center;
    gap: 14px;
    font-family: "Roboto", Arial, sans-serif;
    font-weight: 700;
    font-size: 44px;
    letter-spacing: 3px;
    text-transform: uppercase;
  }
  .wordmark__square { width: 22px; height: 22px; background: var(--green); }
  .card--front .wordmark { top: 66px; color: var(--navy); }
  .card--back .wordmark { top: 120px; color: var(--white); }

  .holder {
    position: absolute;
    left: 35px; right: 35px; top: 203px;
    display: flex;
    align-items: center;
    gap: 8px;
  }
  .holder__rule { flex: 1; height: 1.5px; background: var(--green); }
  .holder__name {
    font-family: "Roboto Condensed", "Arial Narrow", sans-serif;
    font-weight: 700;
    font-size: 20px;
    color: var(--navy);
    white-space: nowrap;
  }

  .contact {
    position: absolute;
    top: 249px;
    font-size: 14px;
    line-height: 19px;
    color: var(--ink);
  }
  .contact--left { left: 35px; }
  .contact--right { right: 35px; text-align: right; }
  .contact__row { display: flex; align-items: center; gap: 8px; }
  .contact__icon { width: 13px; height: 13px; fill: var(--navy); }

  .band {
    position: absolute;
    left: 0; right: 0; bottom: 0;
    height: 30px;
    display: flex;
    justify-content: center;
    align-items: center;
    font-size: 14px;
    letter-spacing: 5.5px;
  }
  .card--front .band { background: var(--navy); color: var(--green); }
  .card--back .band { background: var(--green); color: var(--white); }
  .band strong { font-weight: 700; }
</style>
</head>
<body>

<section class="card card--front">
  <div class="wordmark"><span class="wordmark__square"></span>Veltrow Ledger</div>

  <div class="holder">
    <span class="holder__rule"></span>
    <span class="holder__name">Marcus L. Trenholm, CPA</span>
    <span class="holder__rule"></span>
  </div>

  <div class="contact contact--left">
    <div class="contact__row">
      <svg class="contact__icon" viewBox="0 0 24 24" aria-hidden="true"><path d="M6.6 10.8a15.1 15.1 0 0 0 6.6 6.6l2.2-2.2a1 1 0 0 1 1-.25 11.4 11.4 0 0 0 3.6.57 1 1 0 0 1 1 1V20a1 1 0 0 1-1 1A17 17 0 0 1 3 4a1 1 0 0 1 1-1h3.5a1 1 0 0 1 1 1c0 1.25.2 2.45.57 3.6a1 1 0 0 1-.25 1z"/></svg>
      <span>555-562-0974</span>
    </div>
    <div class="contact__row">
      <svg class="contact__icon" viewBox="0 0 24 24" aria-hidden="true"><path d="M2 5h20v14H2z"/><path d="M3 6l9 7 9-7" fill="none" stroke="var(--paper)" stroke-width="1.6"/></svg>
      <span>marcus@veltrowledger.com</span>
    </div>
  </div>

  <div class="contact contact--right">
    <div>842 E Alder Ave</div>
    <div>Corwin Falls, MN 43827</div>
  </div>

  <div class="band">www.<strong>veltrowledger</strong>.com</div>
</section>

<section class="card card--back">
  <div class="wordmark"><span class="wordmark__square"></span>Veltrow Ledger</div>
  <div class="band">www.<strong>veltrowledger</strong>.com</div>
</section>

</body>
</html>
```